Modern Corporate Brochure For Australian Real Estate Agency

We need a corporate 10 page A4 brochure for a Australian Real Estate agency with information for our clients and referral partners.

Main colour scheme: #238b53

Examples of designs:
https://plateworks.net/item/8-page-corporate-business-brochure/5827134

https://plateworks.net/item/brochure/46715382

https://plateworks.net/item/the-company-profile/73591624

https://plateworks.net/item/brochure-pack-a4trifold-leafletbusiness-card/836517

Target Market(s)

Professional Australians

Industry/Entity Type

Real Estate

Font styles to use
Sans Serif

Requirements
Must have
• Use of multiple greens from the logo

```html
<!DOCTYPE html>
<html lang="en">
<head>
<meta charset="utf-8">
<title>Tallis Property Group – Brochure Pages</title>
<link href="https://fonts.googleapis.com/css2?family=Anton&family=Catamaran:wght@600;700&family=Open+Sans:ital,wght@0,400;0,600;1,400&family=Arimo:wght@700&display=swap" rel="stylesheet">
<style>
:root{
  --bg:#a3a3a3;
  --green:#238b53;
  --leaf:#3aa75f;
  --deep:#1b5e3a;
  --dark:#144a2e;
  --ink:#2b2b2b;
  --tint:#5f9a78;
  --paper:#ffffff;
}
*{margin:0;padding:0;box-sizing:border-box}
html,body{width:1200px;height:1200px;overflow:hidden;background:var(--bg)}
.sheet{position:relative;width:1200px;height:1200px}
.page{position:absolute;width:582px;height:823px;transform:scale(.621);transform-origin:0 0;background:var(--paper);overflow:hidden;font-family:"Open Sans",sans-serif;color:var(--ink)}
.page svg.bg{position:absolute;left:0;top:0;width:582px;height:823px}
.abs{position:absolute}
.title{font-family:"Catamaran",sans-serif;font-weight:700;color:var(--deep);font-size:22px;line-height:1}
.subtitle{font-family:"Catamaran",sans-serif;font-weight:700;color:var(--deep);font-size:13px}
.body{font-size:9.2px;line-height:13px;text-align:justify}
.body p+p{margin-top:12px}
.brand{font-family:"Catamaran",sans-serif;font-weight:600;color:var(--deep);display:flex;align-items:center;gap:8px}
.brand i{display:block;width:14px;height:14px;background:var(--green)}
.welcome{font-family:"Anton",sans-serif;color:var(--deep);font-size:48px;line-height:1;letter-spacing:.5px}
.welcome-name{font-family:"Arimo",sans-serif;font-weight:700;color:var(--deep);font-size:34px;line-height:1}
.url{font-weight:600;font-size:15px;letter-spacing:.6px}
.quote{position:absolute;left:27px;width:526px;border:1px solid var(--deep);border-radius:3px;padding:8px 12px;font-size:9.2px;line-height:13px}
.quote .by{text-align:right;margin-top:4px}
.qmark{position:absolute;font-family:"Catamaran",sans-serif;font-weight:700;color:var(--deep);font-size:26px;line-height:1;background:var(--paper);padding:0 2px}
.mission{font-style:italic;font-size:10px;line-height:13.5px}
.service{position:absolute;left:102px;width:452px}
.service .subtitle{font-size:15px;margin-bottom:3px}
.icon{position:absolute;left:27px;width:54px;height:54px}
.checks{position:absolute;display:grid;grid-template-columns:1fr 1fr;column-gap:20px;font-size:9.2px;line-height:12.5px}
.checks ul{list-style:none}
.checks li{position:relative;padding-left:15px;margin-bottom:5px}
.checks li svg{position:absolute;left:0;top:2px;width:8px;height:8px}
.feature{position:absolute;left:27px;width:526px;display:flex;gap:16px;font-size:9.2px;line-height:13px;text-align:justify}
.feature svg{flex:0 0 42px;height:42px}
.contact{position:absolute;top:720px;font-size:10px;line-height:18px}
.contact h4{font-family:"Catamaran",sans-serif;font-weight:700;color:var(--deep);font-size:13px;line-height:16px}
.contact .row{display:flex;align-items:center;gap:7px}
.contact .row svg{width:11px;height:11px}
</style>
</head>
<body>
<div class="sheet">

  <!-- Cover -->
  <section class="page cover" style="left:28px;top:63px">
    <svg class="bg" viewBox="0 0 582 823">
      <defs>
        <linearGradient id="coverPhoto" x1="0" y1="0" x2="0" y2="1">
          <stop offset="0" stop-color="#f4f7f9"/>
          <stop offset=".35" stop-color="#c9d6df"/>
          <stop offset=".65" stop-color="#a7b3a7"/>
          <stop offset="1" stop-color="#6f7d55"/>
        </linearGradient>
        <linearGradient id="deepFade" x1="0" y1="0" x2="1" y2="1">
          <stop offset="0" stop-color="#1f6b43"/>
          <stop offset="1" stop-color="#0f3f26"/>
        </linearGradient>
      </defs>
      <polygon points="0,0 130,0 18,228 18,823 0,823" fill="url(#deepFade)"/>
      <polygon role="img" aria-label="Photo of a white weatherboard house with picket fence and brick path" points="18,228 30,200 582,200 582,655 18,655" fill="url(#coverPhoto)"/>
      <polygon points="582,590 582,823 445,823" fill="url(#deepFade)"/>
      <rect x="0" y="805" width="455" height="18" fill="var(--dark)"/>
    </svg>
    <div class="abs brand" style="left:298px;top:132px;font-size:20px"><i></i>Tallis Property Group</div>
    <div class="abs welcome" style="left:40px;top:672px">WELCOME TO</div>
    <div class="abs welcome-name" style="left:40px;top:726px">TALLIS PROPERTY GROUP</div>
    <div class="abs url" style="left:40px;top:770px">www.tallisproperty.com.au</div>
  </section>

  <!-- About -->
  <section class="page about" style="left:418px;top:63px">
    <svg class="bg" viewBox="0 0 582 823">
      <defs>
        <linearGradient id="cityA" x1="0" y1="0" x2="0" y2="1">
          <stop offset="0" stop-color="#6f9c82"/><stop offset=".6" stop-color="#2f6e4b"/><stop offset="1" stop-color="#153f28"/>
        </linearGradient>
        <linearGradient id="leafA" x1="0" y1="0" x2="1" y2="1">
          <stop offset="0" stop-color="#2a9a5a"/><stop offset="1" stop-color="#1a6a3e"/>
        </linearGradient>
      </defs>
      <rect role="img" aria-label="Night city skyline reflected on a river, green tint" x="0" y="0" width="582" height="222" fill="url(#cityA)"/>
      <polygon points="0,0 220,0 105,222 0,222" fill="url(#leafA)"/>
      <polygon points="582,630 582,805 470,805" fill="var(--deep)"/>
      <rect x="0" y="805" width="582" height="18" fill="var(--deep)"/>
    </svg>
    <div class="abs title" style="left:27px;top:242px">Tallis Property Group</div>
    <div class="abs subtitle" style="left:27px;top:272px">Innovation through service</div>
    <div class="abs body" style="left:27px;top:292px;width:526px">
      <p>Tallis Property Group are forward thinking property specialists changing the perception the real estate industry has developed by providing a level of service the market deserve, and should expect when trading in a serviced based industry. Growing to now manage over 1000+ properties for 800+ clients within 3 years of operating Tallis Property Group are having an impact to an industry that needs refreshing.</p>
      <p>The real estate industry receives plenty of criticism at times and deservedly so in many cases. It is the goal of Tallis Property Group to change the industry perception for its clients and deliver a level of service we ourselves would expect from a real estate agency. Like most companies Tallis Property Group are represented by its people so regular training and constant internal reviews are provided to uphold our own expectations and brand name.</p>
      <p>We can confidently say that our agency and team will over deliver and outperform other agents for our clientele regardless of market conditions.</p>
    </div>
    <div class="quote" style="top:492px">Many thanks and I hope to deal with you again in the future- you have provided absolutely brilliant service as well as outstanding communication. Thanks again and all the best.<div class="by">MARISA - TENANT</div></div>
    <div class="qmark" style="left:32px;top:478px">&ldquo;</div>
    <div class="qmark" style="left:522px;top:546px">&rdquo;</div>
    <div class="quote" style="top:575px">Thank you Tom Wexley from Tallis Property for your professional approach in selling my house at 12 Wattlebird St Gladstone. I gained maximum price for my investment with minimum fuss. I highly recommend Tom for any realty matters.<div class="by">REID HALLOWAY - GLADSTONE LANDLORD</div></div>
    <div class="qmark" style="left:32px;top:561px">&ldquo;</div>
    <div class="qmark" style="left:522px;top:632px">&rdquo;</div>
    <div class="abs subtitle" style="left:27px;top:666px;font-size:16px">Our Mission</div>
    <div class="abs mission" style="left:27px;top:695px;width:490px">&ldquo;To provide a superior service that is unmatched in the real estate industry and ensure that all Tallis Property Group clients achieve the highest possible yields &amp; sale prices for their properties.&rdquo;</div>
  </section>

  <!-- Services -->
  <section class="page services" style="left:812px;top:63px">
    <svg class="bg" viewBox="0 0 582 823">
      <defs>
        <linearGradient id="cityB" x1="0" y1="0" x2="0" y2="1">
          <stop offset="0" stop-color="#7aa48b"/><stop offset=".55" stop-color="#3b7857"/><stop offset="1" stop-color="#183f2a"/>
        </linearGradient>
      </defs>
      <rect role="img" aria-label="City river and highway at dusk, green tint" x="0" y="0" width="582" height="222" fill="url(#cityB)"/>
      <polygon points="0,0 220,0 105,222 0,222" fill="url(#leafA)"/>
      <polygon points="582,600 582,805 460,805" fill="var(--deep)"/>
      <rect x="0" y="805" width="460" height="18" fill="var(--deep)"/>
    </svg>
    <svg class="icon" style="top:258px" viewBox="0 0 54 54"><circle cx="27" cy="27" r="27" fill="var(--deep)"/><circle cx="27" cy="27" r="22" fill="none" stroke="#fff" stroke-width="1.2"/></svg>
    <div class="service" style="top:256px">
      <div class="subtitle">Residential Property Management</div>
      <div class="body"><p>It is common to find that within the overwhelming majority of real estate offices the property management department is the most under-resourced. It's no wonder investors move from one agency to another in search of a decent property manager and agency to work with.</p><p>Our property managers receive regular training with independent industry professionals and organisations to ensure they are aware of all legislative changes as they are made that allows them to deal with whatever comes their way comfortably and efficiently.</p></div>
    </div>
    <svg class="icon" style="top:398px" viewBox="0 0 54 54"><circle cx="27" cy="27" r="27" fill="var(--deep)"/><circle cx="27" cy="27" r="22" fill="none" stroke="#fff" stroke-width="1.2"/></svg>
    <div class="service" style="top:398px">
      <div class="subtitle">Property Sales</div>
      <div class="body"><p>When selling your property it is important to select an agent who is a part of an agency with a great culture and proven results in selling property regardless of market conditions. Our sales consultants have been selected to work within the Tallis Property Group brand as they have experience within the industry and have constantly outperformed.</p><p>Only elite agents with the right approach to dealing with people in real estate are offered the opportunity to sell through Tallis Property Group to ensure that the culture brand image of the company is respected and well- represented at all times.</p></div>
    </div>
    <svg class="icon" style="top:562px" viewBox="0 0 54 54"><circle cx="27" cy="27" r="27" fill="var(--deep)"/><circle cx="27" cy="27" r="22" fill="none" stroke="#fff" stroke-width="1.2"/></svg>
    <div class="service" style="top:558px;width:410px">
      <div class="subtitle">Development Management</div>
      <div class="body"><p>Development management is a unique service that we provide here at Tallis Property for both smaller and larger developer clients. It is important for the sales agency and rental managers to have some involvement throughout the projects infancy to ensure that demand for the stock will be high to deliver sales and also for those properties sold to investors actually rent and achieve the rental yields promised to investors when making the purchase originally.</p><p>It is crucial to the success of the development and the amount of profit that the development yields that all of these consultants are managed and work well together. Property development can be very exciting and quite lucrative if done correctly and at the right time. If you are considering pursuing a development or require some assistance to do so Tallis Property Group can assist, manage, and deliver a project as development consultants.</p></div>
    </div>
  </section>

  <!-- Brisbane -->
  <section class="page region" style="left:28px;top:613px">
    <svg class="bg" viewBox="0 0 582 823">
      <defs>
        <linearGradient id="cityC" x1="0" y1="0" x2="0" y2="1">
          <stop offset="0" stop-color="#4f7f64"/><stop offset=".5" stop-color="#1f5438"/><stop offset="1" stop-color="#0f2e1d"/>
        </linearGradient>
        <linearGradient id="houseFade" x1="0" y1="0" x2="1" y2="0">
          <stop offset="0" stop-color="#c4b49a"/><stop offset=".45" stop-color="#e6e1d8"/><stop offset="1" stop-color="#f4f4f4"/>
        </linearGradient>
      </defs>
      <rect role="img" aria-label="Aerial night view of the Brisbane city skyline and river, green tint" x="0" y="0" width="582" height="222" fill="url(#cityC)"/>
      <polygon points="0,0 220,0 105,222 0,222" fill="url(#leafA)"/>
      <rect role="img" aria-label="Two-storey suburban house fading into a soft street scene" x="0" y="610" width="582" height="195" fill="url(#houseFade)"/>
      <polygon points="582,590 582,805 470,805" fill="var(--deep)"/>
      <rect x="0" y="805" width="582" height="18" fill="var(--deep)"/>
    </svg>
    <div class="abs title" style="left:27px;top:240px">Brisbane Property Management</div>
    <div class="abs body" style="left:27px;top:272px;width:526px">It is common to find that within the overwhelming majority of real estate offices the property management department is the most under resourced. It's no wonder investors move from one agency to another in search of a decent property manager and agency to work with. If you are experiencing any, or all of the practices listed below then you need to seriously consider moving the management of your property to Tallis Property Group immediately.</div>
    <div class="checks" style="left:27px;top:340px;width:526px">
      <ul>
        <li><svg viewBox="0 0 8 8"><rect x=".5" y=".5" width="7" height="7" fill="none" stroke="var(--green)"/><path d="M2 4l1.5 1.5L6 2.5" fill="none" stroke="var(--green)"/></svg>Extended periods of vacancy</li>
        <li><svg viewBox="0 0 8 8"><rect x=".5" y=".5" width="7" height="7" fill="none" stroke="var(--green)"/><path d="M2 4l1.5 1.5L6 2.5" fill="none" stroke="var(--green)"/></svg>Lower rental yields than you expect</li>
        <li><svg viewBox="0 0 8 8"><rect x=".5" y=".5" width="7" height="7" fill="none" stroke="var(--green)"/><path d="M2 4l1.5 1.5L6 2.5" fill="none" stroke="var(--green)"/></svg>Not receiving routine inspections on time, or at all</li>
        <li><svg viewBox="0 0 8 8"><rect x=".5" y=".5" width="7" height="7" fill="none" stroke="var(--green)"/><path d="M2 4l1.5 1.5L6 2.5" fill="none" stroke="var(--green)"/></svg>A lack of communication from your property manager</li>
        <li><svg viewBox="0 0 8 8"><rect x=".5" y=".5" width="7" height="7" fill="none" stroke="var(--green)"/><path d="M2 4l1.5 1.5L6 2.5" fill="none" stroke="var(--green)"/></svg>Poor service skills when dealing with staff within your managing agency</li>
      </ul>
      <ul>
        <li><svg viewBox="0 0 8 8"><rect x=".5" y=".5" width="7" height="7" fill="none" stroke="var(--green)"/><path d="M2 4l1.5 1.5L6 2.5" fill="none" stroke="var(--green)"/></svg>Dealing with a property manager who isn't intimate with the rental market</li>
        <li><svg viewBox="0 0 8 8"><rect x=".5" y=".5" width="7" height="7" fill="none" stroke="var(--green)"/><path d="M2 4l1.5 1.5L6 2.5" fill="none" stroke="var(--green)"/></svg>A constant turnover of property managers within the agency managing your property</li>
        <li><svg viewBox="0 0 8 8"><rect x=".5" y=".5" width="7" height="7" fill="none" stroke="var(--green)"/><path d="M2 4l1.5 1.5L6 2.5" fill="none" stroke="var(--green)"/></svg>Not having easy access to information such as financial statements, routine reports &amp; leases</li>
      </ul>
    </div>
    <div class="feature" style="top:470px"><svg viewBox="0 0 42 42"><circle cx="21" cy="21" r="19" fill="none" stroke="var(--deep)" stroke-width="3"/><circle cx="21" cy="21" r="12" fill="none" stroke="var(--deep)" stroke-width="3"/><circle cx="21" cy="21" r="5" fill="var(--deep)"/></svg><div>Our property managers receive regular training with independent industry professionals &amp; organisations to ensure they are aware of all legislative changes as they are made that allows them to deal with whatever comes their way comfortably and efficiently.</div></div>
    <div class="feature" style="top:535px"><svg viewBox="0 0 42 42"><rect x="4" y="28" width="5" height="12" fill="var(--deep)"/><rect x="12" y="23" width="5" height="17" fill="var(--deep)"/><rect x="20" y="18" width="5" height="22" fill="var(--deep)"/><rect x="28" y="13" width="5" height="27" fill="var(--deep)"/><path d="M3 24L17 12l6 5L37 4" fill="none" stroke="var(--deep)" stroke-width="3"/></svg><div>Our average vacancy rate at any given time is under 5% and our properties generate 6% higher rents than our competitors. Why is that? Because we strategically aim to have our leases expiring at the right times of the year when demand is at its highest for any particular area. Not all areas are the same, in fact some areas can deliver rental variations of over 10% if not timed/managed correctly.</div></div>
    <div class="abs brand" style="left:318px;top:758px;font-size:14px"><i></i>Tallis Property Group</div>
  </section>

  <!-- Gladstone -->
  <section class="page region" style="left:418px;top:613px">
    <svg class="bg" viewBox="0 0 582 823">
      <defs>
        <linearGradient id="houseTint" x1="0" y1="0" x2="0" y2="1">
          <stop offset="0" stop-color="#9fc2ad"/><stop offset=".5" stop-color="#5e9478"/><stop offset="1" stop-color="#2f6246"/>
        </linearGradient>
      </defs>
      <rect role="img" aria-label="Large two-storey family home among trees, green tint" x="0" y="0" width="582" height="222" fill="url(#houseTint)"/>
      <polygon points="0,0 220,0 105,222 0,222" fill="url(#leafA)"/>
      <rect role="img" aria-label="Two-storey suburban house fading into a soft street scene" x="0" y="610" width="582" height="195" fill="url(#houseFade)"/>
      <polygon points="582,590 582,805 470,805" fill="var(--deep)"/>
      <rect x="0" y="805" width="582" height="18" fill="var(--deep)"/>
    </svg>
    <div class="abs title" style="left:27px;top:242px">Gladstone Property Management</div>
    <div class="abs body" style="left:27px;top:281px;width:526px">It is common to find that within the overwhelming majority of real estate offices the property management department is the most under resourced. It's no wonder investors move from one agency to another in search of a decent property manager and agency to work with. If you are experiencing any, or all of the practices listed below then you need to seriously consider moving the management of your property to Tallis Property Group immediately.</div>
    <div class="checks" style="left:27px;top:349px;width:526px">
      <ul>
        <li><svg viewBox="0 0 8 8"><rect x=".5" y=".5" width="7" height="7" fill="none" stroke="var(--green)"/><path d="M2 4l1.5 1.5L6 2.5" fill="none" stroke="var(--green)"/></svg>Extended periods of vacancy</li>
        <li><svg viewBox="0 0 8 8"><rect x=".5" y=".5" width="7" height="7" fill="none" stroke="var(--green)"/><path d="M2 4l1.5 1.5L6 2.5" fill="none" stroke="var(--green)"/></svg>Lower rental yields than you expect</li>
        <li><svg viewBox="0 0 8 8"><rect x=".5" y=".5" width="7" height="7" fill="none" stroke="var(--green)"/><path d="M2 4l1.5 1.5L6 2.5" fill="none" stroke="var(--green)"/></svg>Not receiving routing inspections on time, or at all</li>
        <li><svg viewBox="0 0 8 8"><rect x=".5" y=".5" width="7" height="7" fill="none" stroke="var(--green)"/><path d="M2 4l1.5 1.5L6 2.5" fill="none" stroke="var(--green)"/></svg>A lack of communication from your property manager</li>
        <li><svg viewBox="0 0 8 8"><rect x=".5" y=".5" width="7" height="7" fill="none" stroke="var(--green)"/><path d="M2 4l1.5 1.5L6 2.5" fill="none" stroke="var(--green)"/></svg>Poor service skills when dealing with staff within your managing agency</li>
      </ul>
      <ul>
        <li><svg viewBox="0 0 8 8"><rect x=".5" y=".5" width="7" height="7" fill="none" stroke="var(--green)"/><path d="M2 4l1.5 1.5L6 2.5" fill="none" stroke="var(--green)"/></svg>Dealing with a property manager who isn't intimate with the rental market</li>
        <li><svg viewBox="0 0 8 8"><rect x=".5" y=".5" width="7" height="7" fill="none" stroke="var(--green)"/><path d="M2 4l1.5 1.5L6 2.5" fill="none" stroke="var(--green)"/></svg>A constant turnover of property managers within the agency managing your property</li>
        <li><svg viewBox="0 0 8 8"><rect x=".5" y=".5" width="7" height="7" fill="none" stroke="var(--green)"/><path d="M2 4l1.5 1.5L6 2.5" fill="none" stroke="var(--green)"/></svg>Not having easy access to information such as financial statements, routine reports &amp; leases</li>
      </ul>
    </div>
    <div class="feature" style="top:485px"><svg viewBox="0 0 42 42"><circle cx="21" cy="21" r="19" fill="none" stroke="var(--deep)" stroke-width="3"/><circle cx="21" cy="21" r="12" fill="none" stroke="var(--deep)" stroke-width="3"/><circle cx="21" cy="21" r="5" fill="var(--deep)"/></svg><div>Our property managers receive regular training with independent industry professionals &amp; organisations to ensure they are aware of all legislative changes as they are made that allows them to deal with whatever comes their way comfortably and efficiently.</div></div>
    <div class="feature" style="top:548px"><svg viewBox="0 0 42 42"><rect x="4" y="28" width="5" height="12" fill="var(--deep)"/><rect x="12" y="23" width="5" height="17" fill="var(--deep)"/><rect x="20" y="18" width="5" height="22" fill="var(--deep)"/><rect x="28" y="13" width="5" height="27" fill="var(--deep)"/><path d="M3 24L17 12l6 5L37 4" fill="none" stroke="var(--deep)" stroke-width="3"/></svg><div>Our average vacancy rate at any given time is under 5% and our properties generate 6% higher rents than our competitors. Why is that? Because we strategically aim to have our leases expiring at the right times of the year when demand is at its highest for any particular area. Not all areas are the same, in fact some areas can deliver rental variations of over 10% if not timed/managed correctly.</div></div>
    <div class="abs brand" style="left:318px;top:758px;font-size:14px"><i></i>Tallis Property Group</div>
  </section>

  <!-- Back cover -->
  <section class="page back" style="left:812px;top:613px">
    <svg class="bg" viewBox="0 0 582 823">
      <defs>
        <linearGradient id="backDeep" x1="0" y1="0" x2="1" y2="1">
          <stop offset="0" stop-color="#1f6e44"/><stop offset=".5" stop-color="#134a2c"/><stop offset="1" stop-color="#2a9a5a"/>
        </linearGradient>
      </defs>
      <rect x="0" y="0" width="582" height="823" fill="url(#backDeep)"/>
      <polygon points="0,0 200,0 0,400" fill="var(--leaf)" opacity=".55"/>
      <polygon points="0,238 535,238 318,673 0,673" fill="var(--paper)"/>
      <polygon points="0,650 330,650 305,700 0,700" fill="var(--deep)"/>
      <rect x="0" y="700" width="582" height="95" fill="var(--paper)"/>
      <rect x="0" y="795" width="582" height="28" fill="var(--deep)"/>
    </svg>
    <div class="abs subtitle" style="left:120px;top:258px;font-size:17px">Tallis Property Group</div>
    <div class="abs body" style="left:55px;top:290px;width:400px;text-align:center">Tallis Property Group is one of Queensland's fastest growing property agencies. Our team are driven, focused, trained, and have proven results delivering better service and achieving superior results for their clients than any other agency in the market place. Our team collectively manage over 600 properties and have over 50 years' experience between them.</div>
    <div class="abs body" style="left:45px;top:380px;width:330px;text-align:left">In total we manage an asset portfolio worth in excess of 200 million and have only been operating since August 2012. Experiencing that kind of growth predominantly via referral means that we must be doing something right. Our clients and associates strongly believe in what we do and appreciate the dedication they receive when allowing Tallis Property Group the opportunity to manage or sell their largest asset.</div>
    <div class="abs brand" style="left:48px;top:582px;font-size:17px"><i></i>Tallis Property Group</div>
    <div class="abs url" style="left:72px;top:625px;font-size:11px">www.tallisproperty.com.au</div>
    <div class="contact" style="left:45px">
      <h4>Brisbane</h4>
      <div class="row"><svg viewBox="0 0 12 12"><circle cx="6" cy="6" r="6" fill="var(--deep)"/><path d="M4 3.2l1 1.8-.6.6a4 4 0 002 2l.6-.6 1.8 1-.6 1.2C5.6 9 3 6.4 2.8 3.8z" fill="#fff"/></svg>(07) 3100 4821</div>
      <div class="row"><svg viewBox="0 0 12 12"><circle cx="6" cy="6" r="6" fill="var(--deep)"/><rect x="3" y="4" width="6" height="4.2" fill="none" stroke="#fff" stroke-width=".8"/><path d="M3 4l3 2.3L9 4" fill="none" stroke="#fff" stroke-width=".8"/></svg>info@tallisproperty.com.au</div>
    </div>
    <div class="contact" style="left:298px">
      <h4>Gladstone</h4>
      <div class="row"><svg viewBox="0 0 12 12"><circle cx="6" cy="6" r="6" fill="var(--deep)"/><path d="M4 3.2l1 1.8-.6.6a4 4 0 002 2l.6-.6 1.8 1-.6 1.2C5.6 9 3 6.4 2.8 3.8z" fill="#fff"/></svg>(07) 4900 2637</div>
      <div class="row"><svg viewBox="0 0 12 12"><circle cx="6" cy="6" r="6" fill="var(--deep)"/><rect x="3" y="4" width="6" height="4.2" fill="none" stroke="#fff" stroke-width=".8"/><path d="M3 4l3 2.3L9 4" fill="none" stroke="#fff" stroke-width=".8"/></svg>reception.gladstone@tallisproperty.com.au</div>
    </div>
  </section>

</div>
</body>
</html>
```